Retro 80's Vinyl Wrap Design for RV Protector Shade

As part of a full restoration, I need to reproduce a design of a retro graphic for an 80's Australian caravan (a 'trailer' in the USA), which will be printed on vinyl and applied to a front protector shade on the caravan.
I am looking for an accurate reproduction of the original design, using similar colours to those used in the past. (EDIT: I have a design submitted that satisfies the reproduction brief. To save people doing exactly the same thing. I am now only looking for original designs, as per the description below).
I'm happy to consider designs that reflect the original 80's design, but show a fresh perspective for those that would like to get creative. This might be a modern take that reflects the period, or perhaps a design that the designer of the day might have gone with if they had the technology we have today to reproduce it in vinyl (the original was hand painted, so had to be kept simple to reproduce it easily). A simple brief is to capture the fun and the vibe of the late 70's/early 80's, as this is what we plan to do in the whole restoration. Any creative design should try to incorporate the green and gold on the side of the van, as these will be retained through the restoration. Preference will be given to a design that can keep the 'Silver Mallard' text in its original font (Bookman Std Italic, customised) and original position position, so other people familiar with the van can recognise the reference to the original design. Search for 'larkvale silver mallard decal' and you'll see plenty examples of the original text online.
In the attached files you'll find a picture of our early 80's caravan that is being restored. In the image the protector shade is painted with two angled stripes and the white has yellowed, and has been highlighted in the image with two red arrows, just to be clear. That is the area I will be covering with this design (printed to vinyl). Also attached are examples of the original design I am looking to reproduce.
The protector shade is 2110mm wide, and 570mm high. Included in these measurements is the aluminium trim around the protector shade, which is 25mm wide.
EDIT: An image named profile.png has been added. This shows a close up of the protector shade the vinyl wrap will be applied to. This is to show the profile of the aluminium sheet the protector shade is made from. The pitch (the distance between two crowns, which effectively is the same distance over one crown and one trough) is 100mm. It is recommended bleed is allowed for in any design. If the design is intended to align a particular distance from the edge of a crown or trough, it is recommended additional bleed is allowed for top and bottom, allowing extra vertical movement so the vinyl can be positioned correctly,

```html
<!DOCTYPE html>
<html lang="en">
<head>
<meta charset="utf-8">
<title>Silver Mallard – Protector Shade Artwork Options</title>
<link rel="stylesheet" href="https://fonts.googleapis.com/css2?family=Libre+Baskerville:wght@400;700&family=Roboto+Condensed:wght@700&display=swap">
<style>
  :root {
    --page: #e6e7e8;
    --frame: #b8b9bb;
    --panel: #ffffff;
    --green: #95cb67;
    --gold: #ecc83f;
    --ink: #231f20;
    --tag-text: #939598;
  }
  html, body {
    margin: 0;
    padding: 0;
    width: 1200px;
    height: 800px;
    overflow: hidden;
    background: var(--page);
  }
  .sheet { display: block; width: 1200px; height: 800px; }
  .artboard-tag rect { fill: var(--panel); }
  .artboard-tag text {
    font-family: "Roboto Condensed", sans-serif;
    font-weight: 700;
    font-size: 24px;
    fill: var(--tag-text);
  }
  .frame { fill: var(--frame); }
  .panel { fill: var(--panel); }
  .stripe-artwork { fill: url(#stripe-tones); }
  .wordmark {
    font-family: "Libre Baskerville", serif;
    font-weight: 700;
    font-size: 62px;
    fill: var(--ink);
  }
  .dim-line { stroke: var(--ink); stroke-width: 1.5; fill: none; }
  .dim-arrow { fill: var(--ink); }
  .dim-label {
    font-family: "Libre Baskerville", serif;
    font-weight: 700;
    font-size: 22px;
    fill: var(--ink);
  }
  .frame-note {
    font-family: "Libre Baskerville", serif;
    font-size: 12px;
    fill: var(--ink);
  }
</style>
</head>
<body>
<svg class="sheet" viewBox="0 0 2048 1365" xmlns="http://www.w3.org/2000/svg">
  <defs>
    <linearGradient id="stripe-tones" x1="0" y1="0" x2="0" y2="1">
      <stop offset="0" stop-color="#95cb67"/>
      <stop offset="0.3" stop-color="#ecc83f"/>
      <stop offset="0.5" stop-color="#f6ecc0"/>
      <stop offset="0.7" stop-color="#ecc83f"/>
      <stop offset="1" stop-color="#95cb67"/>
    </linearGradient>
  </defs>

  <!-- Option one: 50 mm bands -->
  <g class="artboard artboard-one">
    <g class="artboard-tag">
      <rect x="68" y="70" width="79" height="40"/>
      <text x="107.5" y="98" text-anchor="middle">AW1</text>
    </g>

    <line class="dim-line" x1="160" y1="156" x2="1778" y2="156"/>
    <path class="dim-arrow" d="M150,156 l22,-9 v18 Z M1788,156 l-22,-9 v18 Z"/>
    <text class="dim-label" x="1002" y="147" text-anchor="middle">2110 mm</text>

    <line class="dim-line" x1="128" y1="183" x2="128" y2="605"/>
    <path class="dim-arrow" d="M128,173 l-9,22 h18 Z M128,615 l-9,-22 h18 Z"/>
    <text class="dim-label" x="71" y="385" text-anchor="middle">570mm</text>

    <rect class="frame" x="150" y="173" width="1638" height="442"/>
    <rect class="panel" x="170" y="193" width="1600" height="404"/>

    <rect class="stripe-artwork" x="170" y="278" width="1585" height="233" role="img" aria-label="Green and gold stripe artwork: two 50 mm bands above and below a 100 mm white band, rounded at the right end"/>

    <text class="wordmark" x="1300" y="412" textLength="445" lengthAdjust="spacingAndGlyphs">Silver Mallard</text>

    <g class="band-dimensions">
      <g class="dim-arrow">
        <path d="M1790,278 l20,-9 v18 Z"/><path d="M1790,317 l20,-9 v18 Z"/>
        <path d="M1790,356 l20,-9 v18 Z"/><path d="M1790,433 l20,-9 v18 Z"/>
        <path d="M1790,472 l20,-9 v18 Z"/><path d="M1790,511 l20,-9 v18 Z"/>
      </g>
      <path class="dim-line" d="M1808,278 H1835 L1892,297 L1835,317 H1808 M1835,317 L1892,336 L1835,356 H1808 M1835,356 L1886,396 L1835,433 H1808 M1835,433 L1892,453 L1835,472 H1808 M1835,472 L1892,491 L1835,511 H1808"/>
      <text class="dim-label" x="1905" y="308">50 mm</text>
      <text class="dim-label" x="1905" y="344">50 mm</text>
      <text class="dim-label" x="1892" y="405">100 mm</text>
      <text class="dim-label" x="1905" y="463">50 mm</text>
      <text class="dim-label" x="1905" y="499">50 mm</text>
    </g>

    <text class="frame-note" x="161" y="639">Frame: 25mm wide(around)</text>
  </g>

  <!-- Option two: 75 mm bands -->
  <g class="artboard artboard-two" transform="translate(0,637)">
    <g class="artboard-tag">
      <rect x="68" y="86" width="79" height="40"/>
      <text x="107.5" y="114" text-anchor="middle">AW2</text>
    </g>

    <line class="dim-line" x1="160" y1="156" x2="1778" y2="156"/>
    <path class="dim-arrow" d="M150,156 l22,-9 v18 Z M1788,156 l-22,-9 v18 Z"/>
    <text class="dim-label" x="1002" y="147" text-anchor="middle">2110 mm</text>

    <line class="dim-line" x1="128" y1="183" x2="128" y2="605"/>
    <path class="dim-arrow" d="M128,173 l-9,22 h18 Z M128,615 l-9,-22 h18 Z"/>
    <text class="dim-label" x="71" y="385" text-anchor="middle">570mm</text>

    <rect class="frame" x="150" y="173" width="1638" height="442"/>
    <rect class="panel" x="170" y="193" width="1600" height="404"/>

    <rect class="stripe-artwork" x="170" y="238" width="1585" height="312" role="img" aria-label="Green and gold stripe artwork: two 75 mm bands above and below a 100 mm white band, rounded at the right end"/>

    <text class="wordmark" x="1300" y="412" textLength="445" lengthAdjust="spacingAndGlyphs">Silver Mallard</text>

    <g class="band-dimensions">
      <g class="dim-arrow">
        <path d="M1790,238 l20,-9 v18 Z"/><path d="M1790,297 l20,-9 v18 Z"/>
        <path d="M1790,355 l20,-9 v18 Z"/><path d="M1790,433 l20,-9 v18 Z"/>
        <path d="M1790,491 l20,-9 v18 Z"/><path d="M1790,550 l20,-9 v18 Z"/>
      </g>
      <path class="dim-line" d="M1808,238 H1835 L1894,268 L1835,297 H1808 M1835,297 L1894,327 L1835,355 H1808 M1835,355 L1892,396 L1835,433 H1808 M1835,433 L1894,462 L1835,491 H1808 M1835,491 L1894,521 L1835,550 H1808"/>
      <text class="dim-label" x="1912" y="277">75 mm</text>
      <text class="dim-label" x="1912" y="337">75 mm</text>
      <text class="dim-label" x="1898" y="404">100 mm</text>
      <text class="dim-label" x="1912" y="470">75 mm</text>
      <text class="dim-label" x="1912" y="529">75 mm</text>
    </g>

    <text class="frame-note" x="161" y="640">Frame: 25mm wide(around)</text>
  </g>
</svg>
</body>
</html>
```